Founder / concept developer needs business card // Consultant needs VCARD

I need a business card for me as a founding consultant in Berlin. I advise entrepreneurs, especially in the design of business ideas, business plans or financing applications. More information about this in the annexes. My USP: I design / structure complex ideas and projects convincingly so that my client is successful. I want to communicate professionalism, effectiveness and clarity. Colors like from the range BLACK-GRAY-GREEN. I am 27 years old, I have studied business for 7 years. Attachments: - Business card design (only idea, do not focus on it) - Website screenshot (only idea, do not focus on it)

Target Market(s)

Target group: Founder (20-50 yrs, m / w, needy, in "break-up phase") and CONTRACTOR / "financier" (30-55 yrs, m / w, often public service "routine-oriented"). The foundations are in quite different industries: digital, craft, tourism, retail, services, etc. Almost all German.

Industry/Entity Type

Consultant

Contact Information for Business Card

Lukas Brennwald
M. Sc., International Business Administration
Gründungsberater, Konzeptentwickler
www.kelvoran-mitrel.de
Postfach-Zugang@kelvoran.de
Tel. 0481 294 3172

Colors

Designer to choose colors to be used in the design.

Requirements
Must have
• Professionalism, persuasiveness, clarity
Nice to have
• memorability
Should not have
• Schnörkelei

```html
<!DOCTYPE html>
<html lang="de">
<head>
<meta charset="utf-8">
<title>Visitenkarte Lukas Brennwald</title>
<link rel="stylesheet" href="https://fonts.googleapis.com/css2?family=Poppins:wght@400;500&display=swap">
<style>
  :root {
    --stage: #2b2b2b;
    --green: #3ea84a;
    --green-light: #5cc064;
    --green-dark: #2f8a3a;
    --white: #ffffff;
    --ink: #2a2a2a;
    --grey: #6b6b6b;
  }
  * { margin: 0; padding: 0; box-sizing: border-box; }
  html, body {
    width: 1200px; height: 930px; overflow: hidden;
    background: var(--stage);
    font-family: "Poppins", Arial, sans-serif;
  }
  .stage {
    width: 1200px; height: 930px;
    display: flex; flex-direction: column;
    align-items: center; justify-content: center; gap: 50px;
  }
  .card {
    position: relative;
    width: 600px; height: 388px;
    border-radius: 22px;
    overflow: hidden;
  }
  /* Back side */
  .card-back { background: var(--green); }
  .card-back .emblem {
    position: absolute; left: 230px; top: 84px;
    width: 140px; height: 140px;
    border-radius: 8px;
    background: linear-gradient(150deg, var(--green-light), var(--green-dark));
  }
  .card-back .back-url {
    position: absolute; right: 40px; bottom: 34px;
    color: var(--white); font-size: 14px; letter-spacing: 0.3px;
  }
  /* Front side */
  .card-front { background: var(--white); }
  .card-front .emblem {
    position: absolute; left: 92px; top: 122px;
    width: 160px; height: 160px;
    border-radius: 8px;
    background: linear-gradient(150deg, #46b04f, #6aa36e);
  }
  .divider {
    position: absolute; left: 300px; top: 80px;
    width: 1.5px; height: 230px; background: var(--green);
  }
  .details { position: absolute; left: 324px; top: 66px; }
  .name {
    color: var(--green); font-size: 28px; font-weight: 500;
    line-height: 1.1; letter-spacing: 0.3px;
  }
  .degree {
    color: var(--grey); font-size: 12.5px; line-height: 1.35; margin-top: 4px;
  }
  .roles {
    color: var(--ink); font-size: 14.5px; line-height: 1.35; margin-top: 12px;
  }
  .contacts { list-style: none; margin-top: 14px; }
  .contacts li {
    display: flex; align-items: center; gap: 10px;
    color: var(--ink); font-size: 14.5px; line-height: 1.55;
  }
  .contacts svg { width: 11px; height: 11px; flex: none; }
  .accent { color: var(--green); }
</style>
</head>
<body>
<main class="stage">
  <section class="card card-back">
    <div class="emblem" role="img" aria-label="Grünes Würfel-Emblem"></div>
    <p class="back-url">www.kelvoran-mitrel.de</p>
  </section>

  <section class="card card-front">
    <div class="emblem" role="img" aria-label="Grünes Würfel-Emblem"></div>
    <div class="divider"></div>
    <div class="details">
      <h1 class="name">Lukas Brennwald</h1>
      <p class="degree">M. Sc.,<br>International Business Administration</p>
      <p class="roles">Gründungsberater,<br>Konzeptentwickler</p>
      <ul class="contacts">
        <li>
          <svg viewBox="0 0 12 12" aria-hidden="true"><path d="M2.5 1h2l1 2.5-1.3 1a6.5 6.5 0 0 0 3.3 3.3l1-1.3L11 7.5v2A1.5 1.5 0 0 1 9.5 11 8.5 8.5 0 0 1 1 2.5 1.5 1.5 0 0 1 2.5 1z" fill="#3ea84a"/></svg>
          0481 294 3172
        </li>
        <li>
          <svg viewBox="0 0 12 12" aria-hidden="true"><rect x="1" y="2.5" width="10" height="7" rx="1" fill="none" stroke="#3ea84a" stroke-width="1.3"/><path d="M1.5 3l4.5 3.5L10.5 3" fill="none" stroke="#3ea84a" stroke-width="1.3"/></svg>
          Postfach-Zugang@kelvoran.de
        </li>
        <li>
          <svg viewBox="0 0 12 12" aria-hidden="true"><circle cx="6" cy="6" r="5" fill="none" stroke="#3ea84a" stroke-width="1.2"/><ellipse cx="6" cy="6" rx="2.2" ry="5" fill="none" stroke="#3ea84a" stroke-width="1"/><path d="M1 6h10" stroke="#3ea84a" stroke-width="1"/></svg>
          <span>www.<span class="accent">kelvoran-mitrel.de</span></span>
        </li>
      </ul>
    </div>
  </section>
</main>
</body>
</html>
```